Unique Business Card Design

Unique Business Card design for our orthotic and prosthetic company. Our logo is on our website, color is light blue. Unique shape (artificial leg shaped, vertical, etc..) preferred. Logo, business name, individual name and basic demographics needed.

Industry/Entity Type

Business

Contact Information for Business Card

Logo, Industry, Phone # Logo, "Prosthetic & Orthotic Services" Place to add individual name and contact info

Colors
cee9f5

Requirements
Must have
• The icon must be there, placement of "Prosthetic & Orthotic Services" can be moved
Nice to have
• Like the mix of light blue, and a little darker blue. One design included the icons from my website which was a nice touch

```html
<!DOCTYPE html>
<html lang="en">
<head>
<meta charset="utf-8">
<title>FormaLimb Inc. Business Card</title>
<link href="https://fonts.googleapis.com/css2?family=Montserrat:wght@500;600;700;800&family=Cormorant+Garamond:ital,wght@1,600&display=swap" rel="stylesheet">
<style>
  :root {
    --brand-blue: #1b5fb0;
    --light-blue: #cee9f5;
    --bubble-blue: #8fc3ea;
    --ink: #1c1c1c;
    --paper: #ffffff;
    --backdrop: #e6e9ee;
  }
  * { box-sizing: border-box; margin: 0; padding: 0; }
  html, body { width: 1200px; height: 900px; overflow: hidden; }
  body {
    background: var(--backdrop);
    font-family: "Montserrat", Arial, sans-serif;
    position: relative;
  }
  .card {
    position: absolute;
    left: 250px;
    width: 700px;
    height: 400px;
    background: var(--paper);
    border-radius: 26px;
    overflow: hidden;
    box-shadow: 0 10px 30px rgba(0,0,0,0.18);
  }
  .card--front { top: 35px; }
  .card--back { top: 465px; }

  /* Front */
  .brand-mark {
    position: absolute;
    left: 70px; top: 130px;
    width: 140px; height: 140px;
    border-radius: 50%;
    background: var(--brand-blue);
  }
  .brand-lockup { position: absolute; left: 250px; top: 62px; }
  .brand-name {
    font-weight: 800;
    color: var(--brand-blue);
    font-size: 40px;
    letter-spacing: 0.5px;
    line-height: 1;
    white-space: nowrap;
  }
  .brand-rule {
    height: 3px;
    background: var(--brand-blue);
    margin: 6px 0 4px;
  }
  .brand-tagline {
    font-family: "Cormorant Garamond", Georgia, serif;
    font-style: italic;
    font-weight: 600;
    color: var(--brand-blue);
    font-size: 23px;
    white-space: nowrap;
  }
  .service {
    position: absolute;
    width: 130px;
    text-align: center;
  }
  .service__icon {
    width: 64px; height: 64px;
    margin: 0 auto 10px;
    border-radius: 50%;
    background: radial-gradient(circle at 35% 30%, #ffffff 0%, var(--light-blue) 40%, var(--bubble-blue) 100%);
    border: 2px solid #b9daf0;
  }
  .service__label {
    font-weight: 700;
    font-size: 15px;
    color: var(--brand-blue);
    letter-spacing: 0.5px;
  }
  .service--orthotics { left: 195px; top: 270px; }
  .service--prosthetics { left: 375px; top: 200px; }
  .service--vascular { left: 540px; top: 135px; }

  /* Back */
  .back-art { position: absolute; inset: 0; }
  .back-lockup { position: absolute; left: 40px; top: 55px; }
  .back-lockup .brand-name { font-size: 40px; }
  .back-lockup .brand-tagline { font-size: 24px; }
  .contact-list {
    position: absolute;
    left: 40px; top: 200px;
    list-style: none;
  }
  .contact-list li {
    display: flex;
    align-items: center;
    gap: 12px;
    font-size: 17px;
    font-weight: 500;
    color: var(--ink);
    line-height: 25px;
    white-space: nowrap;
  }
  .contact-list svg { width: 14px; height: 14px; flex: none; }
  .web-domain { color: var(--brand-blue); font-weight: 600; }
  .person {
    position: absolute;
    right: 38px; top: 225px;
    text-align: right;
    color: var(--paper);
  }
  .person__name { font-weight: 700; font-size: 28px; }
  .person__title { font-weight: 500; font-size: 17px; margin-bottom: 14px; }
  .person__address { font-weight: 500; font-size: 17px; line-height: 23px; }
</style>
</head>
<body>

<section class="card card--front" aria-label="Business card front">
  <div class="brand-mark"></div>
  <div class="brand-lockup">
    <div class="brand-name">FORMALIMB INC.</div>
    <div class="brand-rule"></div>
    <div class="brand-tagline">Prosthetic &amp; Orthotic Services</div>
  </div>
  <div class="service service--orthotics">
    <div class="service__icon" role="img" aria-label="Orthotics icon: knee joint in a light blue bubble"></div>
    <div class="service__label">ORTHOTICS</div>
  </div>
  <div class="service service--prosthetics">
    <div class="service__icon" role="img" aria-label="Prosthetics icon: standing figure in a light blue bubble"></div>
    <div class="service__label">PROSTHETICS</div>
  </div>
  <div class="service service--vascular">
    <div class="service__icon" role="img" aria-label="Vascular icon: wheelchair symbol in a light blue bubble"></div>
    <div class="service__label">VASCULAR</div>
  </div>
</section>

<section class="card card--back" aria-label="Business card back">
  <svg class="back-art" viewBox="0 0 700 400" aria-hidden="true">
    <path d="M0 372 C120 384 220 376 290 346 C360 306 400 220 440 130 C460 80 480 30 500 0 L700 0 L700 400 L0 400 Z" fill="var(--ink)"/>
    <path d="M14 380 C130 390 230 382 302 350 C374 310 414 222 454 132 C474 82 494 30 514 0 L700 0 L700 400 L0 400 L0 381 Z" fill="var(--paper)"/>
    <path d="M24 386 C140 394 240 386 312 354 C384 314 424 224 464 134 C484 84 504 30 524 0 L700 0 L700 400 L0 400 L0 386 Z" fill="var(--brand-blue)"/>
    <path d="M0 384 C100 390 160 392 240 400 L0 400 Z" fill="var(--brand-blue)"/>
    <path d="M620 0 L700 0 L700 20 C680 12 650 6 620 0 Z" fill="var(--ink)"/>
    <circle cx="575" cy="105" r="92" fill="var(--brand-blue)" stroke="var(--paper)" stroke-width="5"/>
  </svg>

  <div class="back-lockup">
    <div class="brand-name">FORMALIMB INC.</div>
    <div class="brand-rule"></div>
    <div class="brand-tagline">Prosthetic &amp; Orthotic Services</div>
  </div>

  <ul class="contact-list">
    <li>
      <svg viewBox="0 0 14 14"><rect x="3.5" y="1" width="7" height="12" rx="1.5" fill="none" stroke="var(--brand-blue)" stroke-width="1.6"/></svg>
      845-555-0142
    </li>
    <li>
      <svg viewBox="0 0 14 14"><path d="M3 1.5 L5.5 1.5 L6.5 4.5 L5 5.8 C6 8 7.5 9.5 9 10 L10.3 8.5 L13 9.5 L13 12 C7 12.5 1.5 7 3 1.5 Z" fill="var(--brand-blue)"/></svg>
      718.555.0170
    </li>
    <li>
      <svg viewBox="0 0 14 14"><rect x="1" y="5" width="12" height="6" rx="1" fill="var(--brand-blue)"/><rect x="3.5" y="1.5" width="7" height="4" fill="none" stroke="var(--brand-blue)" stroke-width="1.4"/></svg>
      718.555.0139
    </li>
    <li>
      <svg viewBox="0 0 14 14"><rect x="1" y="3" width="12" height="8.5" rx="1" fill="none" stroke="var(--brand-blue)" stroke-width="1.5"/><path d="M1.5 3.5 L7 8 L12.5 3.5" fill="none" stroke="var(--brand-blue)" stroke-width="1.5"/></svg>
      mkalder@formalimbinc.com
    </li>
    <li>
      <svg viewBox="0 0 14 14"><circle cx="7" cy="7" r="5.8" fill="none" stroke="var(--brand-blue)" stroke-width="1.4"/><ellipse cx="7" cy="7" rx="2.5" ry="5.8" fill="none" stroke="var(--brand-blue)" stroke-width="1.2"/><path d="M1.2 7 H12.8" stroke="var(--brand-blue)" stroke-width="1.2"/></svg>
      <span>www.<span class="web-domain">formalimbinc</span>.com</span>
    </li>
  </ul>

  <div class="person">
    <div class="person__name">Miriam Kalder</div>
    <div class="person__title">Orthotist/Prosthetist</div>
    <div class="person__address">2380 Harbor Ave.<br>Riverton, NY 11990</div>
  </div>
</section>

</body>
</html>
```